Local fast-growing company in the service sector

We are looking for a modern business card design, which should also appear on our letterheads

Target Market(s)

Private and industrial sectors

Contact Information for Business Card

Vorname Name
Kellberger Str. 18
73614 Schorndorf
Tel.: 07146-839214-0
Name@agentur-kvtl.de

Colors
9d9d9d
919191
aaaaaa

Requirements
Must have
• The logo (file) in silver

```html
<!DOCTYPE html>
<html lang="de">
<head>
<meta charset="utf-8">
<title>KVTL Visitenkarte</title>
<link rel="stylesheet" href="https://fonts.googleapis.com/css2?family=Roboto:wght@400;500;700&display=swap">
<style>
  :root {
    --page-bg: #ecebe9;
    --card-light: #d9d9d8;
    --card-mid: #c9c9c8;
    --card-dark: #bdbdbc;
    --card-edge: #e6e6e5;
    --silver: #919191;
    --silver-dark: #6f6f6f;
    --text: #4a4a4a;
  }
  html, body {
    margin: 0;
    padding: 0;
    width: 1200px;
    height: 969px;
    overflow: hidden;
    background: var(--page-bg);
    font-family: "Roboto", Arial, sans-serif;
  }
  .business-card {
    position: absolute;
    left: 188px;
    top: 248px;
    width: 872px;
    height: 494px;
    border-radius: 22px;
    background: linear-gradient(135deg, var(--card-light) 0%, var(--card-mid) 55%, var(--card-dark) 100%);
    box-shadow: inset 0 0 0 2px var(--card-edge), 0 8px 30px rgba(0,0,0,0.12);
  }
  .brand {
    position: absolute;
    right: 52px;
    top: 62px;
    display: flex;
    align-items: center;
    gap: 14px;
  }
  .brand-square {
    width: 46px;
    height: 46px;
    background: var(--silver);
  }
  .brand-name {
    font-weight: 700;
    font-size: 62px;
    line-height: 1;
    letter-spacing: 2px;
    color: var(--silver-dark);
  }
  .brand-domain {
    position: absolute;
    right: 52px;
    top: 127px;
    font-size: 19px;
    font-weight: 500;
    letter-spacing: 3px;
    color: var(--silver-dark);
  }
  .contact {
    position: absolute;
    right: 52px;
    top: 260px;
    text-align: right;
    color: var(--text);
  }
  .person-name {
    font-size: 28px;
    line-height: 34px;
    font-weight: 500;
    margin: 0 0 16px;
    letter-spacing: 0.5px;
  }
  .address {
    font-size: 21px;
    line-height: 24px;
    margin: 0 0 17px;
    font-style: normal;
  }
  .contact-line {
    display: flex;
    justify-content: flex-end;
    align-items: center;
    gap: 12px;
    font-size: 20px;
    line-height: 28px;
  }
  .contact-line svg {
    width: 18px;
    height: 18px;
    fill: var(--text);
  }
</style>
</head>
<body>
  <div class="business-card">
    <div class="brand">
      <div class="brand-square"></div>
      <div class="brand-name">KVTL</div>
    </div>
    <div class="brand-domain">agentur-kvtl.de</div>

    <div class="contact">
      <p class="person-name">JONAS KELLER</p>
      <address class="address">Kellberger Str. 18<br>73614 Schorndorf</address>
      <div class="contact-line">
        <span>07146-839214-0</span>
        <svg viewBox="0 0 24 24" aria-hidden="true"><path d="M6.6 10.8a15.1 15.1 0 0 0 6.6 6.6l2.2-2.2c.3-.3.7-.4 1-.2 1.1.4 2.3.6 3.6.6.6 0 1 .4 1 1V20c0 .6-.4 1-1 1C10.6 21 3 13.4 3 4c0-.6.4-1 1-1h3.5c.6 0 1 .4 1 1 0 1.3.2 2.5.6 3.6.1.3 0 .7-.2 1z"/></svg>
      </div>
      <div class="contact-line">
        <span>name@agentur-kvtl.de</span>
        <svg viewBox="0 0 24 24" aria-hidden="true"><path d="M2 5h20v14H2zM3.5 6.5 12 13l8.5-6.5z" fill-rule="evenodd"/></svg>
      </div>
      <div class="contact-line">
        <span>www.agentur-kvtl.de</span>
        <svg viewBox="0 0 24 24" aria-hidden="true"><circle cx="12" cy="12" r="10"/><path d="M12 2c-3 3-3 17 0 20M2 12h20M4.5 7h15M4.5 17h15" fill="none" stroke="#d0d0cf" stroke-width="1.5"/></svg>
      </div>
    </div>
  </div>
</body>
</html>
```